Elegant and modern Wedding Photography brochure

My existing brochure (attached) needs a major facelift. This is one of the main selling tools - it gets emailed to my clients when they make an equiry on what packages i offer and it is printed out and walked through at our first meeting. This brochure is as critical as my website - it needs to sing!

I'm looking for an eye-catching design that says:
Elegant
Modern
Clean
Crisp
Not cutesy or lovey-dovey thanks - we are more sophisticated and professional than that.

Update images to some of the latest weddings I've shot also. Let me know files and resolution you need. I've enabled right-click to download images on my site for a limited time. Please note that I retain copyright and will pursue any breeches.

Http://www.sarahkelbrin.com/Melbourne-wedding-photography
Updates

Thanks for all of your designs! Will take a few days to decide.

Target Market(s)

Australian Women aged 24-44

Industry/Entity Type

Wedding

Font styles to use
Other font styles liked:
• Century Gothic

Requirements
Must have
• Easy to print - does not have to be 6 A4 pages like the existing brochure
Nice to have
• Some full page images - The photos are supposed to be the hero here :-)
Should not have
• Not cutesy or lovey-dovey thanks - we are more sophisticated and professional than that.

No black backgrounds, I prefer a white thanks

No images in organic shaped boxes (like the rectangles in the logo - no thanks).
Keep the lines straight and sharp

```html
<!DOCTYPE html>
<html lang="en">
<head>
<meta charset="utf-8">
<title>Sarah Kelbrin Wedding Photography Brochure</title>
<link rel="stylesheet" href="https://fonts.googleapis.com/css2?family=Questrial&family=Mulish:ital,wght@1,700&display=swap">
<style>
  :root {
    --backdrop: #f3f3f3;
    --margin-grey: #8e8f93;
    --paper: #e9e9eb;
    --ink: #2a2a2a;
    --soft-ink: #8c8c8c;
    --plum: #8a2a91;
    --band: #c9c9cc;
    --rule: #6e6e72;
  }
  * { margin: 0; padding: 0; box-sizing: border-box; }
  html, body { width: 1200px; height: 802px; overflow: hidden; }
  body {
    position: relative;
    background: var(--backdrop);
    font-family: "Questrial", "Century Gothic", sans-serif;
    color: var(--ink);
  }
  .spread-left {
    position: absolute; left: 38px; top: 37px; width: 709px; height: 728px;
    background: var(--margin-grey);
  }
  .page-column {
    position: absolute; left: 128px; top: 0; width: 434px; height: 728px;
    background: var(--paper);
  }
  .hero-photo {
    position: absolute; left: 0; top: 0; width: 434px; height: 278px;
    background: linear-gradient(160deg, #8b7a3e 0%, #6d6a3a 35%, #3f4530 70%, #2e3428 100%);
  }
  .ornament-band {
    position: absolute; height: 19px;
    background: var(--band);
  }
  .page-column .ornament-band { left: 0; top: 278px; width: 434px; }
  .headline {
    position: absolute; left: 0; top: 330px; width: 416px;
    text-align: center; font-size: 22px; line-height: 34px; color: var(--ink);
  }
  .headline .accent { color: var(--plum); font-size: 27px; }
  .selling-points {
    position: absolute; left: 14px; top: 424px; width: 398px;
    list-style: none; font-size: 11px; line-height: 13px; text-align: justify;
  }
  .selling-points li { position: relative; padding-left: 11px; margin-bottom: 10px; }
  .selling-points li::before {
    content: ""; position: absolute; left: 0; top: 5px;
    width: 4px; height: 4px; border-radius: 50%; background: var(--ink);
  }
  .selling-points strong { font-weight: 700; }
  .footer-rule {
    position: absolute; left: 0; top: 628px; width: 434px; height: 1px; background: var(--rule);
  }
  .footer-brand {
    position: absolute; left: 0; top: 638px; width: 132px; text-align: center;
  }
  .brand-square {
    display: block; margin: 2px auto 8px; width: 40px; height: 40px;
    border: 2px solid var(--plum);
  }
  .brand-name { color: var(--plum); font-size: 16px; white-space: nowrap; }
  .contact-list {
    position: absolute; left: 140px; top: 643px; list-style: none;
    font-size: 9.5px; line-height: 20px; color: var(--ink);
  }
  .spread-right {
    position: absolute; left: 748px; top: 37px; width: 415px; height: 728px;
    background: var(--paper);
  }
  .masthead {
    position: absolute; left: 72px; top: 40px; display: flex; align-items: center; gap: 14px;
  }
  .masthead .brand-square { margin: 0; width: 52px; height: 52px; }
  .masthead .brand-name { font-size: 34px; }
  .spread-right .ornament-band { left: 0; width: 415px; }
  .band-top { top: 174px; }
  .band-bottom { top: 491px; }
  .couple-photo {
    position: absolute; left: 0; top: 193px; width: 415px; height: 298px;
    background: linear-gradient(135deg, #7c7c7c 0%, #5a5a5a 40%, #3a3a3a 65%, #b5b5b5 100%);
  }
  .tagline {
    position: absolute; right: 48px; top: 580px;
    font-family: "Mulish", "Century Gothic", sans-serif; font-style: italic; font-weight: 700;
    font-size: 30px; color: var(--plum);
  }
  .site-address {
    position: absolute; right: 16px; top: 700px;
    font-size: 12.5px; letter-spacing: 1px; color: var(--soft-ink);
  }
</style>
</head>
<body>
  <section class="spread-left">
    <div class="page-column">
      <div class="hero-photo" role="img" aria-label="Photo of a laughing bride with bouquet and two bridesmaids in navy gowns under willow trees"></div>
      <div class="ornament-band" role="img" aria-label="Decorative interlaced border band"></div>
      <h1 class="headline">How do you want to remember<br>your <span class="accent">special day</span>?</h1>
      <ul class="selling-points">
        <li>Elegant, stunning, fuss-free photography that doesn't cost the earth will capture those memories for a lifetime!</li>
        <li>Wedding photography packages start from $1650 and are fully inclusive of fun-filled</li>
        <li>creative &amp; journalistic coverage, digital negatives and professionally edited album.</li>
        <li>Contact Sarah today to arrange an informal catch-up, discuss your requirements and</li>
        <li>find out more about the early <strong>booking bonus!</strong></li>
      </ul>
      <div class="footer-rule"></div>
      <div class="footer-brand">
        <span class="brand-square"></span>
        <span class="brand-name">Sarah Kelbrin</span>
      </div>
      <ul class="contact-list">
        <li>Hatherley Lane, Seddon, VIC, 3011</li>
        <li>Web : www.sarahkelbrin.com</li>
        <li>Email: sarah@sarahkelbrin.com</li>
        <li>Mobile: 0412 555 308</li>
      </ul>
    </div>
  </section>

  <section class="spread-right">
    <div class="masthead">
      <span class="brand-square"></span>
      <span class="brand-name">Sarah Kelbrin</span>
    </div>
    <div class="ornament-band band-top" role="img" aria-label="Decorative interlaced border band"></div>
    <div class="couple-photo" role="img" aria-label="Black and white portrait of a smiling bride and groom embracing"></div>
    <div class="ornament-band band-bottom" role="img" aria-label="Decorative interlaced border band"></div>
    <p class="tagline">Love is all you need.</p>
    <p class="site-address">www.sarahkelbrin.com</p>
  </section>
</body>
</html>
```